Thornbury Spa

We are a large Miami Beach spa and salon. I am still building our website but you can use it as a resource to gain a better understanding of who we are ....www.velloraspa-studio.com.

We offer a comprehensive list of services in hair, nails, massage, skin care, tanning, spray tanning and waxing and we offer high quality products for skin care, tanning and hair. We are open 7 days.

We would like to see a clean and simple menu that looks a lot like the one from "The Spa at Larkwood." In particular, we have a copy of a menu from their West Hollywood, CA location that is just beautiful. In the uploaded content you will see a sampling of that menu. We would like to see greys, blacks, silvers, whites and warm colors like reds and oranges. We specifically attempt to remain gender neutral so that we don't attract only girls (with pink colors and flowers etc). The final design should convey a simple, clean, friendly environment and the final product should be sized such that it is 1.) portable and 2.) inexpensive to print. We will be running thousands of these at a time so cost of printing is a consideration.

The booklet consists of two parts: one part is the standard menu with descriptions of services and products and photos etc (think of this as the sales piece that convinces a potential customer to visit) and will be stapled together like you would expect a small menu to be and should resemble the Larkwood menu. The prices should not be included in this part of the booklet that will be printed and stapled. The other part is a single insert and is removable and replaceable. I want this removable insert placed in the last page of the book in a folder pocket or something else that you can think of so that when it's time to change prices here that I am not throwing away all of the booklets....I am only replacing the inserts at the end of the menu booklet. Please design this single page insert so that should a customer remove it from the booklet and keep it, that it stands alone with our name, logo, website and phone number. This page can and probably will have to be 2 sided.

At the back of the booklet, I also want the polices to be printed in one page (think fine print in any sort of business dealing.)

With regard to the look and feel slider of economical v upmarket...we definitely want to convey we deliver upmarket services at reasonable prices. Think, world class services and products at reasonable, everyday prices.

With regard to the uploaded files:
I uploaded both EPS and TIF formats. The colors in those files are not the palette we want at all. The colors we want use for the circular logo must match the standard colors as depicted in the uploaded file "Thornburytanrooms"

Target Market(s)

The target market is the average 20-35 year old in Miami Beach that cares about their appearance. The range of clientele is quite diverse.

Industry/Entity Type

Environment

Requirements
Must have
• It must have elegant and simple photographs that relate to the services being offered. We are selling a service set and an environment...so this menu should be reflect that goal. The logo should be repeated often throughout the book but in subtle ways.

Stock photos are fine as long as they don't seem obviously stock.

Should not have
• Nothing buddha like. Nothing themed. It should be all inclusive and not seek to identify with any particular group or gender.

Nothing that fits the stereotype of "Miami Beach." We want to represent ourselves in the same category as the best spas in the world because we moving everything we do in that direction. Think class!

```html
<!DOCTYPE html>
<html lang="en">
<head>
<meta charset="utf-8">
<title>Thornbury Spa — Massage Menu</title>
<link rel="stylesheet" href="https://fonts.googleapis.com/css2?family=Source+Sans+3:wght@300;400;600&display=swap">
<style>
  :root {
    --spa-red: #e8323c;
    --spa-red-deep: #c01d2b;
    --text-light: #ffffff;
    --frame-line: rgba(200, 200, 200, 0.85);
    --frame-line-red: rgba(255, 220, 220, 0.55);
    --title-grey: #6e6e70;
    --caption-ink: #2a2a2a;
    --band-white: rgba(255, 255, 255, 0.62);
    --brand-tan: #d9b48a;
    --page-bg: #ffffff;
  }
  * { margin: 0; padding: 0; box-sizing: border-box; }
  html, body { width: 1200px; height: 600px; overflow: hidden; background: var(--page-bg); }
  .spread {
    position: relative; width: 1200px; height: 600px; overflow: hidden;
    font-family: "Source Sans 3", "Myriad Pro", Arial, sans-serif;
  }
  .spread__art { position: absolute; inset: 0; }
  .intro-band {
    position: absolute; left: 0; top: 432px; width: 640px; height: 104px;
    background: var(--band-white);
  }
  .section-title {
    position: absolute; left: 31px; top: 464px;
    font-weight: 300; font-size: 44px; letter-spacing: 10px; color: var(--title-grey);
    line-height: 1;
  }
  .section-caption {
    position: absolute; left: 319px; top: 466px; width: 262px;
    font-size: 8.6px; font-weight: 600; letter-spacing: 0.9px; line-height: 10px;
    color: var(--caption-ink);
  }
  .menu {
    position: absolute; left: 709px; top: 0; width: 440px; color: var(--text-light);
  }
  .service { position: absolute; left: 0; width: 440px; }
  .service--stone { top: 64px; }
  .service--sports { top: 250px; }
  .service__head { position: relative; height: 24px; }
  .service__name {
    font-size: 17.5px; font-weight: 400; letter-spacing: -0.2px; line-height: 22px;
    text-transform: uppercase;
  }
  .rate-label {
    position: absolute; top: 5px; font-size: 11.5px; line-height: 14px;
  }
  .rate-label--resident { left: 262px; }
  .rate-label--guest { left: 337px; }
  .service__desc {
    font-size: 9.6px; line-height: 15.6px; letter-spacing: -0.05px;
  }
  .service--stone .service__desc { margin-top: 14px; }
  .price-list { list-style: none; font-size: 9.6px; line-height: 15.6px; }
  .service--stone .price-list { margin-top: 12px; }
  .service--sports .price-list { margin-top: 14px; }
  .price-list li { position: relative; height: 15.6px; }
  .price-list .price { position: absolute; top: 0; }
  .price--resident { left: 262px; }
  .price--guest { left: 337px; }
  .service--stone .price--guest { left: 300px; }
  .brand-mark {
    position: absolute; left: 1022px; top: 524px; width: 144px; text-align: center;
    color: var(--brand-tan);
  }
  .brand-mark__dot {
    display: block; width: 20px; height: 20px; border-radius: 50%;
    background: var(--brand-tan); margin: 0 auto 6px;
  }
  .brand-mark__name {
    display: block; white-space: nowrap;
    font-family: "Source Sans 3", Arial, sans-serif; font-weight: 400;
    font-size: 14px; letter-spacing: 1.5px; text-transform: uppercase; line-height: 18px;
  }
</style>
</head>
<body>
<main class="spread">
  <svg class="spread__art" width="1200" height="600" viewBox="0 0 1200 600">
    <defs>
      <linearGradient id="photoTone" x1="0" y1="0" x2="1" y2="1">
        <stop offset="0" stop-color="#f4f1ee"/>
        <stop offset="0.35" stop-color="#e7c2a6"/>
        <stop offset="0.6" stop-color="#d9a487"/>
        <stop offset="1" stop-color="#efe6df"/>
      </linearGradient>
      <linearGradient id="panelRed" x1="0" y1="0" x2="1" y2="1">
        <stop offset="0" stop-color="#e8323c"/>
        <stop offset="0.55" stop-color="#e02b37"/>
        <stop offset="1" stop-color="#c01d2b"/>
      </linearGradient>
    </defs>
    <rect class="photo-area" x="0" y="0" width="700" height="600" fill="url(#photoTone)"
          role="img" aria-label="Photograph: three guests relaxing face down on white towels with warm basalt stones along their backs"/>
    <path class="menu-panel" d="M665 0 H1200 V600 H552 C620 580 665 520 665 390 Z" fill="url(#panelRed)"/>
    <path class="page-frame" d="M665 18 H19 V578 H600" fill="none" stroke="var(--frame-line)" stroke-width="2"/>
    <path class="page-frame page-frame--on-red" d="M665 18 H1182 V578 H1172 M1016 578 H600" fill="none" stroke="var(--frame-line-red)" stroke-width="2"/>
  </svg>

  <div class="intro-band"></div>
  <h1 class="section-title">MASSAGE</h1>
  <p class="section-caption">Ease into stillness as warm stones and skilled hands melt away tension. Every session is tailored to your body, your pace and your day, leaving you calm, restored and light.</p>

  <section class="menu">
    <article class="service service--stone">
      <div class="service__head">
        <h2 class="service__name">Hot Stone Therapy</h2>
        <span class="rate-label rate-label--resident">Residents</span>
        <span class="rate-label rate-label--guest">Hotel Guests</span>
      </div>
      <p class="service__desc">Experience a deep sense of warmth and relaxation through the use of basalt polished over time by river currents. Our therapists warm these iron-rich stones and utilize their heat to help tense muscles relax, allowing massage therapists to manipulate your muscles more effectively. Hot stone therapy is especially effective at reducing muscular tension, relieving pain and improving circulation.</p>
      <ul class="price-list">
        <li>The 60-Minute Hot Stone Massage<span class="price price--resident">$109.00</span><span class="price price--guest">$125.00</span></li>
        <li>The 90-Minute Hot Stone Massage<span class="price price--resident">$149.00</span><span class="price price--guest">$175.00</span></li>
      </ul>
    </article>

    <article class="service service--sports">
      <div class="service__head">
        <h2 class="service__name">Sports-Specific Massage</h2>
      </div>
      <p class="service__desc">Athletes, whether weekend warriors or world-class competitors, can derive significant health and performance benefits from regular sports-specific massage sessions. Sports-specific massage is a form of massage therapy that helps athletes recover from or avoid sports-related injuries, and typically utilizes more vigorous forms of massage to facilitate muscle healing or relaxation in specific areas. Sports massage therapy should be performed before and especially after a competition to prevent injuries and loss of mobility and to maximize the longevity of your sporting career. Sports-specific massages improve blood flow and nutrient delivery to your muscles, efficiently clear harmful metabolic byproducts, effectively reduce tension in your fascia, reduction of scar tissue formation, improve tissue elasticity and in your tissue's ability to absorb nutrients. It can also reduce stress experienced in and around your joints, ligaments, tendons and muscles.</p>
      <ul class="price-list">
        <li>The 30-Minute Tune-up<span class="price price--resident">$69.00</span><span class="price price--guest">$80.00</span></li>
        <li>The 45-Minute Overhaul<span class="price price--resident">$89.00</span><span class="price price--guest">$105.00</span></li>
      </ul>
    </article>
  </section>

  <div class="brand-mark">
    <span class="brand-mark__dot"></span>
    <span class="brand-mark__name">Thornbury Spa</span>
  </div>
</main>
</body>
</html>
```